Fall Convention Graphic Designs (logo, digital brochure, t-shirt designs, social media templates)

I need a graphic package for the Redwick Movement Guild Autumn Dance Convention. Redwick Movement Guild is a non-profit organization of dance teachers, and this educational dance conference is for members and their students with multiple events throughout the weekend. The convention has a new them each year. I will need a package with a general "logo" type graphic, a digital brochure, t-shirt design, and social media graphic templates. This year's Convention has a general theme and names for each event throughout the weekend.
The theme and event names for this year are:
Convention Theme Twice Around a Waltz: Beneath the Harlow Moons
Registration Desk The Willowgate Nook
Members Welcome A Moonwashed Greeting
Banquet A Velvet Twilight
President's Reception Glow Beyond Dusk
Jr. Member Desk Wanderers' Wharf
Jr. Member Pizza Party Cricket Mixer
Members Luncheon Harlow Reveries

I am attaching a word file that includes information and text to be included in brochure. Also attached are designs from previous years for brochures, T-shirts, and social media graphics.

Colors that we will be using for decorations at various events over the weekend this year are shades of green (fern and mossy green), shades of blue (including navy), white, and pinks (including mauve). The banquet event will be decorated as an enchanted forest. We are using fairy lights, books that look like a storybook, and lanterns for decorations as well. I think I would like a more modern design, and I do not want anything that is childish or too whimsical. While we are using floral decorations I don't want bunches of flowers in the design.

*I am open to seeing initial logo type designs and giving feedback to make sure it is a direction that I like and then moving forward with the other parts of the project.

```html
<!DOCTYPE html>
<html lang="en">
<head>
<meta charset="utf-8">
<title>Redwick Movement Guild Autumn Dance Convention</title>
<link rel="stylesheet" href="https://fonts.googleapis.com/css2?family=Playfair+Display:wght@400;700&family=Arimo:wght@400;700&display=swap">
<style>
:root{
  --stage:#8a8a8c;
  --paper:#ffffff;
  --navy:#1b2452;
  --navy-deep:#121a3d;
  --navy-mid:#283572;
  --gold:#b08a45;
  --gold-bright:#c9a25a;
  --cream:#f2ede4;
  --ink:#2b2b33;
  --white:#ffffff;
}
*{box-sizing:border-box;margin:0;padding:0}
html,body{width:1200px;height:406px;overflow:hidden;background:var(--stage)}
body{position:relative;font-family:"Arimo",Arial,sans-serif}
.page{position:absolute;top:36px;width:260px;height:334px;overflow:hidden;box-shadow:4px 6px 10px rgba(0,0,0,.35)}
.page--cover{left:34px;background:var(--paper)}
.page--poster{left:327px;background:var(--navy)}
.page--themes{left:616px;background:linear-gradient(160deg,var(--navy-mid),var(--navy-deep))}
.page--schedule{left:905px;background:linear-gradient(200deg,var(--navy-mid),var(--navy-deep))}

/* cover */
.wordmark{position:absolute;left:0;right:0;text-align:center;font-family:"Playfair Display",Georgia,serif;font-weight:700}
.page--cover .wordmark{top:140px;font-size:22px;line-height:26px;color:var(--navy)}
.page--cover .wordmark__dot{display:block;width:14px;height:14px;border-radius:50%;background:var(--gold);margin:0 auto 12px}

/* poster */
.poster-scene{position:absolute;inset:0;background:linear-gradient(180deg,#1d2a63 0%,#2b3a86 45%,#3b4aa8 62%,#1a214b 80%,#0f1533 100%)}
.page--poster .wordmark{top:176px;font-size:20px;line-height:24px;color:var(--white)}
.poster-info{position:absolute;top:290px;color:var(--white)}
.poster-info h3{font-size:7px;font-weight:700;margin-bottom:7px}
.poster-info p{font-size:4.3px;line-height:4.8px}
.poster-info--dates{left:15px}
.poster-info--venue{left:131px;width:120px}

/* themes page */
.section-title{font-family:"Playfair Display",Georgia,serif;color:var(--white);text-transform:uppercase;font-weight:400}
.page--themes .section-title--themes{position:absolute;left:17px;top:13px;font-size:12.5px;line-height:12px}
.names-table{position:absolute;left:17px;top:44px;width:226px;border-collapse:collapse;font-size:5.3px}
.names-table th{background:var(--gold);color:var(--white);text-align:left;font-weight:700;height:14.5px;padding-left:8px;font-size:6px}
.names-table td{height:15.8px;padding-left:8px;color:var(--ink)}
.names-table tr:nth-child(odd) td{background:var(--white)}
.names-table tr:nth-child(even) td{background:var(--cream)}
.names-table td:first-child,.names-table th:first-child{width:96px;border-right:1px solid var(--gold)}
.section-title--schedule{position:absolute;left:17px;top:195px;font-size:12.5px}
.sparkle{position:absolute;background:radial-gradient(ellipse at center,rgba(214,170,80,.85) 0%,rgba(176,138,69,.45) 40%,rgba(176,138,69,0) 70%)}
.sparkle--themes{left:160px;top:200px;width:110px;height:140px}
.sparkle--schedule{left:190px;top:-10px;width:80px;height:110px}

.day{position:absolute;left:17px}
.day__icon{position:absolute;left:0;top:0;width:20px;height:20px;background:var(--gold);display:flex;align-items:center;justify-content:center}
.day__body{margin-left:26px;color:var(--white)}
.day__title{color:var(--gold-bright);font-size:6.4px;font-weight:700;margin-bottom:3px}
.day__line{font-size:4.6px;line-height:6px}
.day__line--bold{font-weight:700;margin-top:3px}
.day--thu{top:214px}
.day--fri{top:258px}
.day-rule{position:absolute;left:17px;top:249px;width:175px;border-top:.5px solid rgba(255,255,255,.4)}

/* schedule page */
.day__venue{font-size:4.6px;margin-bottom:3px;color:var(--white)}
.agenda{display:grid;grid-template-columns:44px 1fr;font-size:4.5px;line-height:6.1px}
.agenda dt{color:var(--gold-bright)}
.agenda dd{color:var(--white)}
.day--sat{top:19px;left:17px}
.day--sun{top:103px;left:17px}
.day-rule--sat{top:93px;left:42px;width:180px}
.section-title--info{position:absolute;left:17px;top:168px;font-size:12px}
.info{position:absolute;left:17px;top:184px;width:226px;color:var(--white);font-size:4.1px;line-height:4.7px;text-align:justify}
.info p{margin-bottom:4.5px}
.faculty{position:absolute;left:17px;top:299px;width:226px;height:23px;border:1px solid var(--gold);display:flex;align-items:center;padding:0 8px;gap:10px}
.faculty__lead{font-family:"Playfair Display",Georgia,serif;color:var(--gold-bright);font-size:6px;white-space:nowrap;text-transform:uppercase}
.faculty__list{color:var(--white);font-size:4.1px;line-height:4.8px}
</style>
</head>
<body>

<section class="page page--cover">
  <div class="wordmark"><span class="wordmark__dot"></span>Redwick<br>Movement Guild</div>
</section>

<section class="page page--poster">
  <div class="poster-scene" role="img" aria-label="Moonlit night sky over a forest lake with stars"></div>
  <div class="wordmark">Redwick<br>Movement Guild</div>
  <div class="poster-info poster-info--dates">
    <h3>November 19 – 22, 2026</h3>
    <p>Brightmoor Convention Center<br>Lindenhall Grand Hotel<br>Aldermont, NC</p>
  </div>
  <div class="poster-info poster-info--venue">
    <h3>Teacher’s Intensive on Friday</h3>
    <p>Outstanding accommodations at the<br>Lindenhall Grand Hotel<br>4580 Ferrow Lane, Aldermont, NC 27999<br>Call for reservations and mention RMG for your best rate!<br>555-014-2290 or book online.</p>
  </div>
</section>

<section class="page page--themes">
  <div class="sparkle sparkle--themes" role="img" aria-label="Gold glitter star decoration"></div>
  <h2 class="section-title section-title--themes">Convention Theme &amp;<br>Event Names</h2>
  <table class="names-table">
    <thead><tr><th>EVENT</th><th>NAME</th></tr></thead>
    <tbody>
      <tr><td>Convention Theme</td><td>Twice Around a Waltz: Beneath the Harlow Moons</td></tr>
      <tr><td>Registration Desk</td><td>The Willowgate Nook</td></tr>
      <tr><td>Members Welcome</td><td>A Moonwashed Greeting</td></tr>
      <tr><td>Banquet</td><td>A Velvet Twilight</td></tr>
      <tr><td>President's Reception</td><td>Glow Beyond Dusk</td></tr>
      <tr><td>Jr. Member Desk</td><td>Wanderers' Wharf</td></tr>
      <tr><td>Jr. Member Pizza Party</td><td>Cricket Mixer</td></tr>
      <tr><td>Members Luncheon</td><td>Harlow Reveries</td></tr>
    </tbody>
  </table>

  <h2 class="section-title section-title--schedule">Schedule of Events</h2>
  <div class="day day--thu">
    <div class="day__icon"><svg width="10" height="10" viewBox="0 0 10 10"><rect x="1" y="2" width="8" height="7" fill="none" stroke="#fff" stroke-width=".8"/><path d="M1 4h8M3 1v2M7 1v2" stroke="#fff" stroke-width=".8"/></svg></div>
    <div class="day__body">
      <div class="day__title">THURSDAY, NOVEMBER 19TH</div>
      <div class="day__line">Solo Title Scholarship Competition Audition Classes, Interviews,<br>and Opening Number Rehearsals</div>
      <div class="day__line day__line--bold">A Moonwashed Greeting– Members Welcome Party</div>
    </div>
  </div>
  <div class="day-rule"></div>
  <div class="day day--fri">
    <div class="day__icon"><svg width="10" height="10" viewBox="0 0 10 10"><rect x="1" y="2" width="8" height="7" fill="none" stroke="#fff" stroke-width=".8"/><path d="M1 4h8M3 1v2M7 1v2" stroke="#fff" stroke-width=".8"/></svg></div>
    <div class="day__body">
      <div class="day__title">FRIDAY, NOVEMBER 20TH</div>
      <div class="day__line">Teachers Intensive<br>Solo Title Scholarship Competition Audition Classes, Interviews,<br>and Opening Number Rehearsals<br>Registration Packet Pickup<br>Solo Title Scholarship Competition and Crowning</div>
      <div class="day__line day__line--bold">Cricket Mixer - Jr. Members Pizza and Pajama Party</div>
    </div>
  </div>
</section>

<section class="page page--schedule">
  <div class="sparkle sparkle--schedule" role="img" aria-label="Gold glitter star decoration"></div>
  <div class="day day--sat">
    <div class="day__icon"><svg width="10" height="10" viewBox="0 0 10 10"><rect x="1" y="2" width="8" height="7" fill="none" stroke="#fff" stroke-width=".8"/><path d="M1 4h8M3 1v2M7 1v2" stroke="#fff" stroke-width=".8"/></svg></div>
    <div class="day__body">
      <div class="day__title">SATURDAY, NOVEMBER 21ST</div>
      <div class="day__venue">Lindenhall Grand Hotel, Brightmoor Convention Center</div>
      <dl class="agenda">
        <dt>8:00am</dt><dd>The Willowgate Nook Registration Desk Opens</dd>
        <dt>8:00am</dt><dd>Wanderers' Wharf Junior Member Desk Opens</dd>
        <dt>8:00am-8:45am</dt><dd>Junior Member Banquet Performance Rehearsal</dd>
        <dt>9:00am-1:00pm</dt><dd>Convention Classes  Mini</dd>
        <dt>9:00am-3:00pm</dt><dd>Convention Classes  Junior | Senior | Teachers &amp; Assistants</dd>
        <dt>6:00pm-7:30pm</dt><dd>Banquet – A Velvet Twilight</dd>
        <dt>8:30pm</dt><dd>Miss and Mr. Talent and Crowning</dd>
        <dt>10:00pm</dt><dd>Glow Beyond Dusk - President’s Reception<br>(Immediately following Miss / Mr. Dance Crowning)</dd>
      </dl>
    </div>
  </div>
  <div class="day-rule day-rule--sat"></div>
  <div class="day day--sun">
    <div class="day__icon"><svg width="10" height="10" viewBox="0 0 10 10"><rect x="1" y="2" width="8" height="7" fill="none" stroke="#fff" stroke-width=".8"/><path d="M1 4h8M3 1v2M7 1v2" stroke="#fff" stroke-width=".8"/></svg></div>
    <div class="day__body">
      <div class="day__title">SUNDAY, NOVEMBER 22ND</div>
      <div class="day__venue">Lindenhall Grand Hotel, Brightmoor Convention Center</div>
      <dl class="agenda">
        <dt>7:30am</dt><dd>Contract Signing for New Title Holders</dd>
        <dt>8:00am-9:00am</dt><dd>Judges Critiques for New Title Holders</dd>
        <dt>9:00am-1:00pm</dt><dd>Convention Classes  Mini | Junior | Senior | Teachers &amp; Assistants</dd>
        <dt>1:00pm-2:00pm</dt><dd>Junior Member Special Class</dd>
        <dt>1:00pm</dt><dd>Harlow Reveries– Members Luncheon (Must be Pre-Registered)</dd>
        <dt>2:00pm</dt><dd>Grand Body Meeting</dd>
      </dl>
    </div>
  </div>

  <h2 class="section-title section-title--info">Valuable Information</h2>
  <div class="info">
    <p>Classroom Attire: Students &amp; teachers should be dressed in proper dance attire; leotards, tights and appropriate dance shoes. Cover ups must be worn at all times when leaving class and walking through the hotel. Tap shoes are not allowed outside of the classroom. No bare midriffs please.</p>
    <p>One badge for a parent/monitor will be given to each studio that registers Mini &amp; Junior students (one for each classroom). These people, designated by your studio, will be responsible for your Mini &amp; Junior students concerning bathroom, changing shoes, conduct, etc. Banquet Attire: Semi-formal or formal attire for students, formal attire for teachers and parents.</p>
    <p>Recommended Ages: Mini 6-3, Junior 9-13, Senior 14 &amp; up, Advanced is intended for teaching professionals. Pageant program books, banquet tickets and t-shirts must be pre-ordered. **T-shirts are NOT included with Registration and must be preordered ($25). A very limited number will be available on site**Contestants in Solo Title Scholarship Competition are required to attend all classes in their age level.</p>
    <p>All members' dues must have been post-marked by September 1, 2026 to receive the member rate. You must also pre-register for the Members Luncheon on Sunday. Video recording of classes will be allowed. Video recording and photos during pageant IS NOT ALLOWED. Faculty names will be added in headshots for each of these people once confirmed.</p>
    <p>Teachers Intensive – Featured Guest and underneath Friday November 20th</p>
  </div>
  <div class="faculty">
    <span class="faculty__lead">Noreen Castell</span>
    <span class="faculty__list">Noreen Castell, Priya Halvorsen, Tessa Marlow, Jolene Akerby Voss, Dorian Pell,<br>To Be Determined #1, Noreen Castell</span>
  </div>
</section>

</body>
</html>
```